THE KINDRED LANTERN

project description

The Kindred Lantern was created to challenge the lack of meaning and values in power of mainstream media.

This website will be a platform through which you can explore the meaning of humanity, through a variety of lenses - philosophy, politics, science, art, human interest stories, etc.

As an organization, TKL aims to further the understanding of the meaning of humanity, including its spiritual and existential challenges in 21st century. We wish to inspire and develop this understanding, while transforming mass media and “visual” spaces so they display the beauty and interconnectedness of human beings.

We believe that the kindred lantern and that our “visual” space and mass media should reflect and support those values.

We are looking to create an image that may be seen on the site independently, full screen - or as the background to the home page (with text on top of it, potentially.)
Updates

 

 The city/the background with the advertisementshouldn’t be to depressing because (indigo blue or light gray color) so overall, the page has a pleasant soft look and feel.

 

Also place the boy is looking at needs to have advertisement

 

Thank you

Target Market(s)

people that are sophisticated, modern, engage, care, awere, who are interested scholarly discussions of media, philosophy,art/desighn community - as well as the human spirit.

Industry/Entity Type

Media

Requirements
Must have
• I have photos of a boy looking up. I would like to take this image (pick one) and incorporate into a city scene - one with buildings littered with mass media information and adds - similar to the look of NYC's Vell Plaza. He is looking up a bit overwhelmed trying to make sense of the world he is seeing.
Nice to have
• However, the city scene in the background may be sketched or distorted
Should not have
• should not be agresive or too busy

```html
<!DOCTYPE html>
<html lang="en">
<head>
<meta charset="utf-8">
<title>TKL – The Kindred Lantern</title>
<link href="https://fonts.googleapis.com/css2?family=Arimo:wght@400;700&family=Roboto+Condensed:wght@400;700&display=swap" rel="stylesheet">
<style>
  :root {
    --black: #000000;
    --bar-top: #1c1c1c;
    --bar-bottom: #050505;
    --white: #ffffff;
    --panel: #e6e6e6;
    --ink: #111111;
    --muted: #8a8a8a;
    --rule: #555555;
    --accent: #d40000;
    --sky: #a9c4d8;
    --city-mid: #6d7480;
    --city-dark: #2b2d33;
    --taxi: #c9a24a;
  }
  * { margin: 0; padding: 0; box-sizing: border-box; }
  html, body { width: 1200px; height: 900px; overflow: hidden; background: var(--black); }
  .page { position: relative; width: 1200px; height: 900px; background: var(--black); font-family: "Arimo", Arial, sans-serif; }

  /* top navigation */
  .nav-bar {
    position: absolute; left: 0; top: 113px; width: 1200px; height: 30px;
    background: linear-gradient(var(--bar-top), var(--bar-bottom));
    font-family: "Roboto Condensed", Arial, sans-serif; font-weight: 700;
    font-size: 8.5px; color: var(--white); letter-spacing: 0.1px;
  }
  .brand-mark { position: absolute; left: 297px; top: 10px; font-size: 10px; }
  .brand-sep { position: absolute; left: 331px; top: 10px; width: 1px; height: 10px; background: #777; }
  .brand-name { position: absolute; left: 339px; top: 11px; }
  .nav-links { position: absolute; left: 538px; top: 11px; display: flex; align-items: center; }
  .nav-links span { white-space: nowrap; }
  .nav-links .pipe { width: 1px; height: 7px; background: #888; margin: 0 11px; }
  .social { display: flex; gap: 5px; margin-left: 6px; }
  .social i { display: block; width: 10px; height: 10px; background: #5a8fc4; border-radius: 1px; }
  .social i:nth-child(3) { background: #e07a22; }
  .social i:nth-child(5) { background: #c23a2e; }

  /* hero */
  .hero {
    position: absolute; left: 0; top: 143px; width: 1200px; height: 366px;
    border-top: 2px solid var(--white); border-bottom: 2px solid var(--white);
    background:
      radial-gradient(ellipse 180px 260px at 590px 300px, rgba(255,255,255,0.75), rgba(255,255,255,0) 70%),
      linear-gradient(to bottom, rgba(0,0,0,0) 72%, rgba(201,162,74,0.55) 88%, rgba(60,50,40,0.6) 100%),
      linear-gradient(to right, var(--city-dark) 0%, var(--city-mid) 22%, var(--sky) 45%, var(--sky) 55%, var(--city-mid) 75%, var(--city-dark) 100%);
  }

  /* logo band */
  .logo-band { position: absolute; left: 0; top: 509px; width: 1200px; height: 86px; background: var(--black); }
  .logo-lockup { position: absolute; left: 477px; top: 18px; display: flex; align-items: flex-end; gap: 8px; color: var(--white); font-family: "Roboto Condensed", Arial, sans-serif; font-weight: 700; }
  .logo-initials { font-size: 64px; line-height: 52px; letter-spacing: -1px; }
  .logo-words { font-size: 20px; line-height: 17px; }

  /* content */
  .content { position: absolute; left: 0; top: 595px; width: 1200px; height: 166px; background: var(--panel); color: var(--ink); }
  .column { position: absolute; top: 11px; font-size: 7px; line-height: 8.7px; }
  .column h2 { font-size: 9.5px; font-weight: 700; line-height: 11px; margin-bottom: 3px; }
  .column p + p { margin-top: 8.5px; }
  .column p + h2 { margin-top: 10px; }
  .col-welcome { left: 298px; width: 215px; }
  .col-work { left: 538px; width: 172px; }
  .col-video { left: 733px; width: 170px; }
  .divider { position: absolute; top: 12px; width: 1px; height: 143px; background: var(--rule); }
  .divider.one { left: 524px; } .divider.two { left: 719px; }

  .video-player { position: relative; width: 170px; height: 106px; margin-top: 3px; background: var(--black); border: 2px solid #222; }
  .video-frame { position: absolute; left: 2px; top: 2px; width: 162px; height: 88px; background: radial-gradient(ellipse at 60% 40%, #6a6f78, #2a2c31 70%); }
  .video-play { position: absolute; left: 71px; top: 28px; }
  .video-label { position: absolute; left: 0; top: 78px; width: 166px; text-align: center; font-size: 8px; font-weight: 700; color: #bbb; }
  .video-controls { position: absolute; left: 2px; top: 90px; width: 162px; height: 11px; background: #1a1a1a; display: flex; align-items: center; font-size: 7px; color: #ddd; }
  .video-controls .track { width: 55px; height: 3px; background: #666; margin: 0 10px 0 5px; position: relative; }
  .video-controls .track::before { content: ""; position: absolute; left: 0; top: 0; width: 25px; height: 3px; background: #eee; }
  .video-controls .time { margin-left: 4px; letter-spacing: 0.3px; }

  /* footer */
  .footer { position: absolute; left: 0; top: 761px; width: 1200px; height: 139px; background: var(--black); font-size: 6.5px; }
  .copyright { position: absolute; left: 297px; top: 8px; color: var(--muted); }
  .newsletter { position: absolute; left: 578px; top: 6px; display: flex; align-items: center; color: var(--white); }
  .newsletter input { width: 105px; height: 11px; margin-left: 8px; border: none; background: var(--white); }
  .newsletter button { width: 86px; height: 11px; margin-left: 3px; border: none; background: var(--accent); color: var(--white); font: 6.5px "Arimo", Arial, sans-serif; }
</style>
</head>
<body>
<div class="page">
  <header class="nav-bar">
    <span class="brand-mark">TKL</span>
    <span class="brand-sep"></span>
    <span class="brand-name">THE KINDRED LANTERN</span>
    <nav class="nav-links">
      <span>WHO WE ARE</span><span class="pipe"></span>
      <span>DONATE NOW!</span><span class="pipe"></span>
      <span>LOGIN</span><span class="pipe"></span>
      <span>CONTACT US</span><span class="pipe"></span>
      <span>FIND US ON</span>
      <span class="social"><i></i><i></i><i></i><i></i><i></i><i></i></span>
    </nav>
  </header>

  <div class="hero" role="img" aria-label="A small boy seen from behind stands in a busy city plaza, looking up at towering buildings covered in glowing billboards and screens while yellow taxis blur past"></div>

  <section class="logo-band">
    <div class="logo-lockup">
      <span class="logo-initials">TKL</span>
      <span class="logo-words">THE<br>KINDRED<br>LANTERN</span>
    </div>
  </section>

  <main class="content">
    <div class="column col-welcome">
      <h2>WELCOME TO TKL</h2>
      <p>Lorem ipsum dolor sit amet, consectetur adipiscing elit. Sed sollicitudin aliquam neque. Suspendisse potenti. Phasellus nec vulputate ipsum. Phasellus tincidunt ante non elit laoreet sollicitudin. Cras diam sem, sollicitudin eu dictum ac, convallis vel ante. In lobortis, risus ac dignissim euismod, enim sapien dictum lorem, et tempus mi felis sit amet nibh. Pellentesque varius semper enim ac aliquet. In hac habitasse platea dictumst.</p>
      <p>Aliquam vitae nunc in nibh accumsan varius sed a nulla. Sed non pellentesque ligula. Sed dignissim imperdiet purus at fringilla. Cum sociis natoque penatibus et magnis dis parturient montes, nascetur ridiculus mus. Nulla blandit magna vitae turpis dictum ornare. Donec tempor iaculis velit, vitae interdum mauris luctus id. Vestibulum aliquet massa ac lorem laoreet elementum scelerisque leo cursus. Donec hendrerit mollis urna in blandit.</p>
    </div>
    <span class="divider one"></span>
    <div class="column col-work">
      <h2>SAMPLE WORK1</h2>
      <p>Lorem ipsum dolor sit amet, consectetur adipiscing elit. Sed sollicitudin aliquam neque. Suspendisse potenti. Phasellus nec vulputate ipsum. Phasellus tincidunt ante non elit laoreet sollicitudin. Cras diam sem, sollicitudin eu dictum ac, convallis vel ante. In lobortis, risus ac dignissim euismod, enim sapien dictum lorem.</p>
      <h2>SAMPLE WORK2</h2>
      <p>Lorem ipsum dolor sit amet, consectetur adipiscing elit. Sed sollicitudin aliquam neque. Suspendisse potenti. Phasellus nec vulputate ipsum. Phasellus tincidunt ante non elit laoreet sollicitudin. Cras diam sem, sollicitudin eu dictum ac, convallis vel ante.</p>
    </div>
    <span class="divider two"></span>
    <div class="column col-video">
      <h2>SAMPLE WORK3</h2>
      <div class="video-player">
        <div class="video-frame" role="img" aria-label="Video still of a city plaza at night lit by billboards"></div>
        <svg class="video-play" width="28" height="32" viewBox="0 0 28 32" aria-hidden="true"><polygon points="2,2 26,16 2,30" fill="#ffffff" fill-opacity="0.85"/></svg>
        <span class="video-label">PLAY VIDEO</span>
        <div class="video-controls">
          <svg width="10" height="8" viewBox="0 0 10 8" aria-hidden="true" style="margin-left:4px"><polygon points="2,1 8,4 2,7" fill="#ddd"/></svg>
          <span class="track"></span>
          <span class="time">00:13 / 02:06</span>
          <svg width="18" height="8" viewBox="0 0 18 8" aria-hidden="true" style="margin-left:6px"><polygon points="1,3 3,3 6,0 6,8 3,5 1,5" fill="#ddd"/><polygon points="8,7 17,1 17,7" fill="#888"/></svg>
        </div>
      </div>
    </div>
  </main>

  <footer class="footer">
    <span class="copyright">© 2011 TKL.&nbsp; All rights reserved.</span>
    <form class="newsletter">
      <label for="news-email">Register your email with us to recieve update</label>
      <input id="news-email" type="email">
      <button type="button">Subscribe to our newsletter</button>
    </form>
  </footer>
</div>
</body>
</html>
```